Business Card Design

New business card design

Target Market(s)

Residential & Commercial Property Managers

Industry/Entity Type

Plumbing Services

Contact Information for Business Card

Name - Rowan Keddle, title - Director, Phone Number - 0431 286 517, email - rowan@tbk-plumbing.com.au, Company ABN - 73 215 904 386,

Font styles to use
Sans Serif

Colors
0054AA
0677BA
7BADD7
CADEEF
E8F1F8

```html
<!DOCTYPE html>
<html lang="en">
<head>
<meta charset="utf-8">
<title>TBK Plumbing Services – Business Card</title>
<link rel="stylesheet" href="https://fonts.googleapis.com/css2?family=Poppins:wght@300;400&display=swap">
<style>
  :root {
    --page-bg: #e9ebee;
    --card-dark: #1f242b;
    --accent-blue: #00aeef;
    --text-light: #ffffff;
    --disc-light: #f1f1f2;
    --disc-mid: #c9c9cc;
    --brand-ink: #1f242b;
  }
  * { box-sizing: border-box; margin: 0; padding: 0; }
  html, body {
    width: 1200px;
    height: 900px;
    overflow: hidden;
    background: var(--page-bg);
    font-family: "Poppins", sans-serif;
  }
  .business-card {
    position: absolute;
    left: 100px;
    top: 141px;
    width: 1000px;
    height: 618px;
    background: var(--card-dark);
    overflow: hidden;
    box-shadow: 0 18px 40px rgba(0, 0, 0, 0.18);
  }
  .accent-band {
    position: absolute;
    top: 0;
    right: 0;
    width: 274px;
    height: 100%;
    background: var(--accent-blue);
  }
  .brand-disc {
    position: absolute;
    left: 501px;
    top: 83px;
    width: 450px;
    height: 450px;
    border-radius: 50%;
    background: radial-gradient(circle at 45% 40%, var(--disc-light) 0%, #dedee0 55%, var(--disc-mid) 100%);
    display: flex;
    flex-direction: column;
    align-items: center;
    justify-content: center;
    color: var(--brand-ink);
    font-weight: 400;
  }
  .brand-name {
    font-size: 96px;
    line-height: 1;
    letter-spacing: 4px;
  }
  .brand-tagline {
    margin-top: 18px;
    font-size: 14px;
    letter-spacing: 12px;
    text-transform: lowercase;
  }
  .contact-person {
    position: absolute;
    left: 45px;
    top: 80px;
  }
  .person-name {
    color: var(--accent-blue);
    font-weight: 300;
    font-size: 37px;
    line-height: 1;
    letter-spacing: 0.5px;
    text-transform: uppercase;
  }
  .person-title {
    color: var(--text-light);
    font-size: 26px;
    line-height: 1.2;
    margin-top: 4px;
  }
  .company-abn {
    position: absolute;
    left: 42px;
    top: 348px;
    font-size: 27px;
    color: var(--text-light);
  }
  .company-abn .abn-label { color: var(--accent-blue); }
  .contact-list {
    position: absolute;
    left: 45px;
    top: 482px;
    list-style: none;
    color: var(--text-light);
    font-size: 27px;
    line-height: 35px;
  }
  .contact-list li {
    display: flex;
    align-items: center;
    gap: 10px;
  }
  .contact-icon {
    width: 28px;
    height: 28px;
    flex: none;
  }
</style>
</head>
<body>
  <main class="business-card">
    <div class="accent-band"></div>

    <div class="brand-disc">
      <span class="brand-name">TBK</span>
      <span class="brand-tagline">plumbing services</span>
    </div>

    <header class="contact-person">
      <h1 class="person-name">Rowan Keddle</h1>
      <p class="person-title">Director</p>
    </header>

    <p class="company-abn"><span class="abn-label">Company ABN</span> 73 215 904 386</p>

    <ul class="contact-list">
      <li>
        <svg class="contact-icon" viewBox="0 0 24 24" aria-hidden="true">
          <path fill="#00aeef" d="M6.6 10.8a15.1 15.1 0 0 0 6.6 6.6l2.2-2.2c.3-.3.7-.4 1-.2 1.1.4 2.3.6 3.6.6.6 0 1 .4 1 1V20c0 .6-.4 1-1 1A17 17 0 0 1 3 4c0-.6.4-1 1-1h3.5c.6 0 1 .4 1 1 0 1.3.2 2.5.6 3.6.1.3 0 .7-.2 1z"/>
          <path fill="none" stroke="#00aeef" stroke-width="1.6" stroke-linecap="round" d="M14 3.5a7 7 0 0 1 6.5 6.5M14 7a3.5 3.5 0 0 1 3 3"/>
        </svg>
        <span>0431 286 517</span>
      </li>
      <li>
        <svg class="contact-icon" viewBox="0 0 24 24" aria-hidden="true">
          <rect x="1.5" y="5" width="21" height="14" fill="#00aeef"/>
          <path d="M1.5 5l10.5 8 10.5-8M1.5 19l8-7M22.5 19l-8-7" fill="none" stroke="#1f242b" stroke-width="1.4"/>
        </svg>
        <span>rowan@tbk-plumbing.com.au</span>
      </li>
    </ul>
  </main>
</body>
</html>
```